Brookvale Building Company - advertisement poster

I am looking to print some canvas signs to advertise my general contracting company, Brookvale Building Company. The sign will measure 6' long x 3' high so the size should match that ratio. I already have a logo icon, which is the Letter 'B' and some trees that I would like to incorporate, see attached. I would also like the to have the following information listed:
1) phone number: 831-555-0172
2) email: brookvalebuildingcompany@mailnest.example
3) website: brookvalebuildingcompany.example
4) Lic#4826130
5) I want to use this text: "BUILD WITH THE B-CREW!"

The ad should be relatively simple and clean. Black and Green are my company colors. I am open to creative ideas!

Target Market(s)

People looking to renovate their homes

Industry/Entity Type

Construction

Colors
59FF00
82FF00
B8FF75
E3FFCB
F4FFEA

Requirements
Must have
• Must have my company logo
Should not have
• No photos or complex graphics

```html
<!DOCTYPE html>
<html lang="en">
<head>
<meta charset="utf-8">
<title>Brookvale Building Company – Canvas Sign</title>
<link rel="stylesheet" href="https://fonts.googleapis.com/css2?family=Archivo:wdth,wght@100..125,400..900&family=Michroma&display=swap">
<style>
  :root {
    --page-bg: #e4e4e4;
    --sign-bg: #323133;
    --sign-bg-soft: #3a393b;
    --brand-green: #6cb544;
    --ink-white: #ffffff;
    --ink-dark: #1f1f20;
  }
  * { margin: 0; padding: 0; box-sizing: border-box; }
  html, body {
    width: 1200px; height: 640px; overflow: hidden;
    background: var(--page-bg);
  }
  .sign {
    position: absolute; left: 6px; top: 23px;
    width: 1188px; height: 594px;
    background: var(--sign-bg);
    overflow: hidden;
    color: var(--ink-white);
  }
  .license-tab {
    position: absolute; right: 0; top: 0;
    width: 354px; height: 77px;
    background: var(--brand-green);
    clip-path: polygon(0 0, 100% 0, 100% 100%, 19% 100%);
  }
  .license-number {
    position: absolute; right: 36px; top: 0; height: 77px;
    display: flex; align-items: center;
    font-family: "Archivo", sans-serif;
    font-weight: 800; font-stretch: 125%;
    font-size: 25px; letter-spacing: 1.5px;
    color: var(--ink-white);
  }
  .brand-mark {
    position: absolute; left: 549px; top: 110px;
    width: 90px; height: 90px;
    background: var(--brand-green);
  }
  .brand-name {
    position: absolute; left: 0; right: 0; top: 222px;
    text-align: center;
    font-family: "Michroma", sans-serif;
    font-weight: 400; font-size: 38px; line-height: 48px;
    letter-spacing: 3px;
    color: var(--ink-white);
  }
  .phone-rules {
    position: absolute; left: 0; top: 0;
    width: 1188px; height: 594px;
  }
  .phone {
    position: absolute; left: 0; right: 0; top: 322px;
    text-align: center;
    font-family: "Michroma", sans-serif;
    font-size: 46px; line-height: 60px; letter-spacing: 5px;
    color: var(--ink-white);
  }
  .phone-flourish {
    position: absolute; left: 464px; top: 394px;
    width: 260px; height: 26px;
    background: var(--sign-bg-soft);
    border-radius: 4px;
  }
  .tagline {
    position: absolute; left: 0; right: 0; top: 428px;
    text-align: center;
    font-family: "Archivo", sans-serif;
    font-weight: 900; font-stretch: 125%;
    font-size: 54px; line-height: 68px; letter-spacing: 3px;
    color: var(--ink-white);
  }
  .tagline-accent { color: var(--brand-green); }
  .contact-bar {
    position: absolute; left: 82px; top: 509px;
    width: 1022px; height: 53px;
    background: var(--ink-white);
    border-radius: 27px;
    display: flex; align-items: center; justify-content: center;
    gap: 28px;
    font-family: "Archivo", sans-serif;
    font-weight: 500; font-size: 21px;
    color: var(--ink-dark);
  }
  .contact-divider {
    width: 2px; height: 26px; background: var(--ink-dark);
  }
</style>
</head>
<body>
  <main class="sign">
    <div class="license-tab"></div>
    <div class="license-number">Lic#4826130</div>

    <div class="brand-mark"></div>
    <h1 class="brand-name">BROOKVALE<br>BUILDING COMPANY</h1>

    <svg class="phone-rules" viewBox="0 0 1188 594" aria-hidden="true">
      <polyline points="174,333 257,333 297,400 429,400" fill="none" stroke="#6cb544" stroke-width="3"/>
      <polyline points="1012,333 929,333 884,399 757,399" fill="none" stroke="#ffffff" stroke-width="3"/>
    </svg>
    <p class="phone">831.555.0172</p>
    <div class="phone-flourish" role="img" aria-label="Small wave-and-dot ornament under the phone number"></div>

    <p class="tagline">BUILD WITH THE <span class="tagline-accent">B-CREW!</span></p>

    <div class="contact-bar">
      <span class="contact-email">brookvalebuildingcompany@mailnest.example</span>
      <span class="contact-divider"></span>
      <span class="contact-web">www.brookvalebuildingcompany.example</span>
    </div>
  </main>
</body>
</html>
```